Super elegant, crisp & clean Business card design required

We recently upgraded our branding - which is on our website - talvendoraphoto.com

I would like a simple, yet elegant, clean business card design please.

The font of my logo is Cinzel - and because of the natural colour - it's best to have this on a black background.

I would like to have the back of the business card - with simply my logo.

PLEASE DO NOT SUBMIT A COMPLICATED / UNCLEAN DESIGN

Industry/Entity Type

Business

Contact Information for Business Card

Talven Doroshko Photography

Font styles to use
Other font styles liked:
• Cinzel

Requirements
Must have
• A backpage with nothing but my logo
• Simple design - stands out
Should not have
• Colour that dont align with my logo
• Over complicated '/ non symmetrical design

```html
<!DOCTYPE html>
<html lang="en">
<head>
<meta charset="utf-8">
<title>Talven Doroshko Photography – Business Card</title>
<link rel="stylesheet" href="https://fonts.googleapis.com/css2?family=Cinzel:wght@400;500&family=Roboto:wght@300;400&display=swap">
<style>
  :root {
    --page-bg: #e9e6df;
    --card-white: #fbfbfa;
    --black-deep: #0f0e0c;
    --black-soft: #24221e;
    --taupe-dark: #968c6f;
    --taupe-mid: #b1a88d;
    --taupe-light: #d6cfb4;
    --ink-taupe: #8f8567;
    --ink-light: #ffffff;
    --rivet: #d9d9d9;
  }
  * { box-sizing: border-box; margin: 0; padding: 0; }
  html, body { width: 1200px; height: 858px; overflow: hidden; }
  body {
    background: var(--page-bg);
    display: flex;
    align-items: center;
    justify-content: center;
    gap: 56px;
  }
  .card {
    position: relative;
    width: 540px;
    height: 309px;
    border-radius: 4px;
    box-shadow: 0 10px 28px rgba(40, 34, 20, 0.25);
    overflow: hidden;
  }
  /* Front */
  .card--front { background: var(--card-white); }
  .owner {
    position: absolute;
    left: 200px;
    top: 40px;
    display: flex;
    align-items: center;
    gap: 10px;
  }
  .owner__icon { width: 30px; height: 30px; flex: none; }
  .owner__name {
    font-family: "Cinzel", serif;
    font-size: 21px;
    color: var(--ink-taupe);
    letter-spacing: 1px;
    line-height: 1;
    white-space: nowrap;
  }
  .owner__role {
    font-family: "Cinzel", serif;
    font-size: 10px;
    color: var(--ink-taupe);
    letter-spacing: 2px;
    margin-top: 5px;
  }
  .brand-panel {
    position: absolute;
    left: 22px;
    top: 112px;
    width: 268px;
    height: 176px;
    border-radius: 7px;
    background: linear-gradient(135deg, var(--black-soft) 0%, var(--black-deep) 100%);
    display: flex;
    align-items: center;
    justify-content: center;
  }
  .rivet {
    position: absolute;
    width: 7px; height: 7px;
    border-radius: 50%;
    background: radial-gradient(circle at 35% 35%, #fff, var(--rivet) 60%, #9a9a9a);
  }
  .rivet--tl { left: 12px; top: 12px; }
  .rivet--tr { right: 12px; top: 12px; }
  .rivet--bl { left: 12px; bottom: 12px; }
  .rivet--br { right: 12px; bottom: 12px; }
  .brand {
    text-align: center;
    font-family: "Cinzel", serif;
    color: var(--taupe-light);
  }
  .brand__name {
    font-size: 18px;
    font-weight: 400;
    letter-spacing: 1px;
    line-height: 1.2;
    white-space: nowrap;
  }
  .brand__tag {
    font-size: 9px;
    letter-spacing: 6px;
    margin-top: 6px;
    padding-left: 6px;
  }
  .contact-list {
    position: absolute;
    left: 306px;
    top: 112px;
    width: 216px;
    display: flex;
    flex-direction: column;
    gap: 14px;
    list-style: none;
  }
  .contact-item {
    height: 40px;
    border-radius: 6px;
    background: linear-gradient(90deg, var(--taupe-dark), var(--taupe-mid));
    display: flex;
    align-items: center;
    gap: 8px;
    padding: 0 10px;
    font-family: "Roboto", sans-serif;
    font-weight: 300;
    font-size: 12px;
    color: var(--ink-light);
    letter-spacing: 0.3px;
    white-space: nowrap;
  }
  .contact-item svg { width: 18px; height: 18px; flex: none; }
  /* Back */
  .card--back {
    background: linear-gradient(150deg, var(--black-soft) 0%, var(--black-deep) 70%);
    display: flex;
    align-items: center;
    justify-content: center;
  }
  .card--back .brand__name { font-size: 26px; }
  .card--back .brand__tag { font-size: 12px; letter-spacing: 9px; padding-left: 9px; margin-top: 8px; }
</style>
</head>
<body>
  <section class="card card--front" aria-label="Business card front">
    <div class="owner">
      <svg class="owner__icon" viewBox="0 0 30 30" aria-hidden="true">
        <circle cx="15" cy="15" r="15" fill="var(--ink-taupe)"/>
        <circle cx="15" cy="11" r="5" fill="#fff"/>
        <path d="M6 24c1.5-5 5-7 9-7s7.5 2 9 7z" fill="#fff"/>
      </svg>
      <div>
        <div class="owner__name">Talven Doroshko</div>
        <div class="owner__role">Owner</div>
      </div>
    </div>

    <div class="brand-panel">
      <span class="rivet rivet--tl"></span><span class="rivet rivet--tr"></span>
      <span class="rivet rivet--bl"></span><span class="rivet rivet--br"></span>
      <div class="brand">
        <p class="brand__name">Talven Doroshko</p>
        <p class="brand__tag">Photography</p>
      </div>
    </div>

    <ul class="contact-list">
      <li class="contact-item">
        <svg viewBox="0 0 18 18" aria-hidden="true">
          <rect x="2" y="4" width="14" height="11" rx="2" fill="#fff"/>
          <rect x="4" y="6" width="10" height="3" fill="var(--taupe-dark)"/>
          <rect x="4" y="10.5" width="2" height="2" fill="var(--taupe-dark)"/>
          <rect x="8" y="10.5" width="2" height="2" fill="var(--taupe-dark)"/>
          <rect x="12" y="10.5" width="2" height="2" fill="var(--taupe-dark)"/>
        </svg>
        07700900417
      </li>
      <li class="contact-item">
        <svg viewBox="0 0 18 18" aria-hidden="true">
          <circle cx="9" cy="9" r="8" fill="#fff"/>
          <ellipse cx="9" cy="9" rx="3.5" ry="7" fill="none" stroke="var(--taupe-dark)" stroke-width="1"/>
          <line x1="2" y1="9" x2="16" y2="9" stroke="var(--taupe-dark)" stroke-width="1"/>
        </svg>
        www.talvendoraphoto.com
      </li>
      <li class="contact-item">
        <svg viewBox="0 0 18 18" aria-hidden="true">
          <rect x="2" y="4" width="14" height="10" rx="1.5" fill="#fff"/>
          <path d="M2.5 4.5 9 10l6.5-5.5" fill="none" stroke="var(--taupe-dark)" stroke-width="1.2"/>
        </svg>
        info@talvendoraphoto.com
      </li>
    </ul>
  </section>

  <section class="card card--back" aria-label="Business card back">
    <div class="brand">
      <p class="brand__name">Talven Doroshko</p>
      <p class="brand__tag">Photography</p>
    </div>
  </section>
</body>
</html>
```